Birchline Septic Solutions

Would like to see some single sided ones but would also like to see some double sided with one sided only being the logo. Owners name is Colin Vandro. Phone number is 555-214-0387
Services are pumping, inspections, installs, and repairs

Contact Information for Business Card

555-241-0387 Colin Vandro Larkmoor, NV

```html
<!DOCTYPE html>
<html lang="en">
<head>
<meta charset="utf-8">
<title>Birchline Septic Solutions – Business Card</title>
<link rel="stylesheet" href="https://fonts.googleapis.com/css2?family=Montserrat:wght@500;600;800&display=swap">
<style>
  :root {
    --page-bg: #2b2b2e;
    --card-bg: #1d1d1f;
    --teal: #2bb7b2;
    --white: #ffffff;
    --emboss: #2a2a2d;
  }
  * { margin: 0; padding: 0; box-sizing: border-box; }
  html, body {
    width: 1200px; height: 948px; overflow: hidden;
    background: var(--page-bg);
    font-family: "Montserrat", sans-serif;
  }
  .sheet {
    width: 1200px; height: 948px;
    display: flex; flex-direction: column;
    align-items: center; justify-content: center; gap: 36px;
  }
  .card {
    position: relative;
    width: 735px; height: 420px;
    background: var(--card-bg);
    border-radius: 26px;
    border-bottom: 5px solid var(--teal);
    overflow: hidden;
    box-shadow: 0 18px 40px rgba(0,0,0,.45);
  }
  /* Logo-only side */
  .card--back { display: flex; align-items: center; justify-content: center; }
  .wordmark {
    font-weight: 800; text-transform: uppercase; line-height: 1.05;
    text-align: center;
  }
  .wordmark--emboss { color: var(--emboss); font-size: 58px; letter-spacing: 2px; }
  .wordmark--emboss small { display: block; font-size: 24px; letter-spacing: 8px; }

  /* Contact side */
  .card--front .brand {
    position: absolute; left: 70px; top: 140px; width: 270px;
    color: var(--white);
  }
  .card--front .wordmark { font-size: 40px; letter-spacing: 1px; }
  .card--front .wordmark small { display: block; font-size: 16px; letter-spacing: 5px; margin-top: 4px; }
  .divider {
    position: absolute; left: 375px; top: 110px;
    width: 1px; height: 150px; background: var(--teal);
  }
  .contact { position: absolute; left: 405px; top: 118px; }
  .contact__name {
    color: var(--teal); font-weight: 800; font-size: 34px;
    text-transform: uppercase; letter-spacing: .5px;
  }
  .contact__city { color: var(--white); font-weight: 500; font-size: 22px; margin-top: 4px; }
  .contact__phone {
    display: flex; align-items: center; gap: 12px;
    color: var(--white); font-weight: 600; font-size: 30px; margin-top: 16px;
  }
  .contact__phone svg { width: 26px; height: 26px; fill: var(--teal); }
  .stripes { position: absolute; left: 0; bottom: 0; width: 735px; height: 110px; }
</style>
</head>
<body>
<main class="sheet">
  <section class="card card--back" aria-label="Card back">
    <p class="wordmark wordmark--emboss">Birchline<small>Septic Solutions</small></p>
  </section>

  <section class="card card--front" aria-label="Card front">
    <div class="brand">
      <p class="wordmark">Birchline<small>Septic Solutions</small></p>
    </div>
    <span class="divider"></span>
    <div class="contact">
      <p class="contact__name">Colin Vandro</p>
      <p class="contact__city">Larkmoor, NV</p>
      <p class="contact__phone">
        <svg viewBox="0 0 24 24" aria-hidden="true"><path d="M6.6 10.8a15.1 15.1 0 0 0 6.6 6.6l2.2-2.2a1 1 0 0 1 1-.25 11.4 11.4 0 0 0 3.6.57 1 1 0 0 1 1 1V20a1 1 0 0 1-1 1A17 17 0 0 1 3 4a1 1 0 0 1 1-1h3.5a1 1 0 0 1 1 1c0 1.25.2 2.45.57 3.6a1 1 0 0 1-.25 1z"/></svg>
        555-241-0387
      </p>
    </div>
    <svg class="stripes" viewBox="0 0 735 110" aria-hidden="true">
      <polygon points="0,72 352,72 330,104 0,104" fill="var(--white)"/>
      <polygon points="380,20 735,20 735,104 350,104" fill="var(--teal)"/>
      <polygon points="0,98 735,98 735,110 0,110" fill="var(--card-bg)"/>
    </svg>
  </section>
</main>
</body>
</html>
```